Ravnaas-Lilleby Group AS

We need a design for our company including background pictures on our web (wix-template), redesign of logo and reports. Our company delivers personality test and services to clients when hiring staff or related to organizatonal developement.

Target Market(s)

Unisex, Age 30-50, managers in private corporations

Industry/Entity Type

Recruitment

Logo Text

Bygger laget sterkt (english translate: buids your team strong)

Number of Pages Required

1 page

Font styles to use
Sans Serif

Colors
add136
34a6d7
0255a3

Requirements
Must have
• The ideal designer will be the one to bring my narrative come to life. And it will have to include the testresults report and redesign (!) of my logo. Following the attached brief in ppt:
• - the testresult report
• - redesign logo
• - graphic elements in a maritime narrative
• - including the boat, the radar, 7 GULLs, the compass etc
Nice to have
• A strong narrative with a lot of elements.
• I really like the green color in the attached breif ;-)

```html
<!DOCTYPE html>
<html lang="en">
<head>
<meta charset="utf-8">
<title>Ravnaas-Lilleby Group AS – Recruitment and Organizational development</title>
<link rel="stylesheet" href="https://fonts.googleapis.com/css2?family=Roboto:wght@400;500;700;900&family=Open+Sans:wght@400;600&display=swap">
<style>
  :root {
    --navy: #23398a;
    --ink: #222222;
    --white: #ffffff;
    --green: #2f9a3f;
    --red: #e0313c;
    --dial-blue: #3d63b8;
    --footer: #1b1b1d;
    --footer-text: #d6d6d6;
    --rule: #3a3a3d;
  }
  * { box-sizing: border-box; margin: 0; padding: 0; }
  html, body { width: 1200px; height: 2486px; overflow: hidden; }
  body { position: relative; background: var(--white); font-family: "Open Sans", Arial, sans-serif; color: var(--ink); }

  .hero {
    position: absolute; left: 0; top: 0; width: 1200px; height: 567px;
    background: linear-gradient(180deg, #5a5a52 0%, #6d6a5c 22%, #8a7f66 40%, #5b5b55 60%, #3f403d 100%);
  }
  .site-nav { position: absolute; left: 0; top: 47px; width: 1200px; height: 84px; background: var(--white); }
  .brand { position: absolute; left: 92px; top: 16px; display: flex; align-items: center; gap: 10px; }
  .brand-mark { width: 20px; height: 20px; background: var(--navy); }
  .brand-name { font-family: "Roboto", sans-serif; font-weight: 900; font-size: 34px; line-height: 40px; color: var(--navy); letter-spacing: 1px; }
  .brand-tag { position: absolute; left: 102px; top: 58px; font-family: "Roboto", sans-serif; font-size: 11px; font-weight: 700; color: var(--navy); }
  .nav-links { position: absolute; left: 266px; top: 31px; display: flex; gap: 30px; list-style: none;
    font-family: "Roboto", sans-serif; font-size: 16px; font-weight: 500; color: var(--ink); }
  .nav-tools { position: absolute; left: 956px; top: 33px; display: flex; align-items: center; gap: 22px; font-family: "Roboto", sans-serif; font-size: 16px; font-weight: 500; }
  .lang { display: flex; align-items: center; gap: 8px; }

  .hero-title { position: absolute; top: 222px; width: 1200px; text-align: center;
    font-family: "Roboto", sans-serif; font-weight: 700; font-size: 86px; line-height: 100px; color: var(--white); letter-spacing: 1px; }
  .hero-sub { position: absolute; top: 324px; width: 1200px; text-align: center;
    font-family: "Open Sans", sans-serif; font-size: 26px; color: var(--white); }

  .feature-band { position: absolute; left: 0; width: 1200px; height: 115px; background: var(--navy); }
  .feature-band.top { top: 567px; }
  .feature-band.bottom { top: 2007px; }
  .feature { position: absolute; top: 0; height: 115px; color: var(--white); }
  .feature svg { position: absolute; left: 0; top: 16px; }
  .feature h3 { position: absolute; left: 70px; top: 16px; white-space: nowrap; font-family: "Roboto", sans-serif; font-weight: 500; font-size: 18px; }
  .feature p { position: absolute; left: 70px; top: 50px; width: 260px; font-size: 13.5px; line-height: 20px; }
  .divider { position: absolute; top: 15px; width: 1px; height: 85px; background: rgba(255,255,255,0.35); }

  .compass-dial { position: absolute; left: 456px; top: 826px; width: 300px; height: 300px; border-radius: 50%;
    background: radial-gradient(circle, #3a3f4e 0%, #5f75b0 35%, #a9b8de 62%, #eef1f8 85%, #ffffff 100%); }
  .compass-point { position: absolute; width: 60px; margin-left: -30px; text-align: center;
    font-family: "Roboto", sans-serif; font-weight: 500; font-size: 38px; line-height: 44px; color: var(--ink); }

  .gauge-label { position: absolute; top: 1220px; width: 240px; text-align: center;
    font-family: "Roboto", sans-serif; font-weight: 500; font-size: 20px; }
  .gauge { position: absolute; top: 1264px; }

  .results-head { position: absolute; top: 1371px; height: 54px; display: flex; align-items: center; gap: 12px;
    font-family: "Roboto", sans-serif; font-weight: 700; font-size: 20px; }
  .result-table { position: absolute; top: 1447px; border-collapse: collapse; width: 239px; }
  .result-table td { width: 50%; height: 45.6px; text-align: center; color: var(--white);
    font-family: "Roboto", sans-serif; font-weight: 700; font-size: 15px; border: 1px solid rgba(255,255,255,0.55); }
  .yes { background: var(--green); }
  .no { background: var(--red); }
  .scores { position: absolute; left: 545px; top: 1447px; width: 110px; list-style: none; }
  .scores li { height: 48.5px; line-height: 40px; text-align: center; font-size: 16px; color: var(--ink); }

  .profile { position: absolute; left: 470px; top: 1764px; width: 580px; font-size: 15px; line-height: 24px; }
  .profile dt { position: absolute; width: 118px; text-align: right; color: var(--ink); }
  .profile dd { margin-left: 152px; width: 430px; margin-bottom: 25px; }

  .site-footer { position: absolute; left: 0; top: 2122px; width: 1200px; height: 364px; background: var(--footer); color: var(--footer-text); }
  .footer-title { position: absolute; top: 82px; font-family: "Roboto", sans-serif; font-weight: 500; font-size: 19px; color: var(--white); }
  .about { position: absolute; left: 99px; top: 118px; width: 410px; font-size: 14px; line-height: 25px; }
  .socials { position: absolute; left: 99px; top: 204px; display: flex; gap: 8px; }
  .socials span { width: 33px; height: 33px; border: 1px solid #8a8a8a; border-radius: 50%; }
  .quick-links { position: absolute; left: 575px; top: 118px; list-style: none; font-size: 12.5px; line-height: 25px; }
  .contact-list { position: absolute; left: 797px; top: 114px; list-style: none; font-size: 12.5px; line-height: 21px; }
  .contact-list li { position: relative; padding-left: 31px; margin-bottom: 20px; }
  .contact-list svg { position: absolute; left: 0; top: 3px; }
  .footer-rule { position: absolute; left: 99px; top: 294px; width: 1000px; height: 1px; background: var(--rule); }
  .copyright { position: absolute; top: 320px; width: 1200px; text-align: center; font-size: 12px; }
</style>
</head>
<body>

<header>
  <div class="hero" role="img" aria-label="Photo of a harbour city skyline at sunset seen from a hill"></div>
  <nav class="site-nav">
    <a class="brand"><span class="brand-mark"></span><span class="brand-name">RLG</span></a>
    <span class="brand-tag">Rekruttering og utvikling</span>
    <ul class="nav-links">
      <li>Take the PAT test</li><li>Jobs</li><li>product Presentation</li><li>Company Presentation</li><li>Contact Us</li>
    </ul>
    <div class="nav-tools">
      <svg width="15" height="15" viewBox="0 0 15 15"><circle cx="6" cy="6" r="4.5" fill="none" stroke="#222" stroke-width="2"/><line x1="9.5" y1="9.5" x2="14" y2="14" stroke="#222" stroke-width="2"/></svg>
      <span class="lang">
        <svg width="22" height="13" viewBox="0 0 22 13"><rect width="22" height="13" fill="#012169"/><path d="M0 0L22 13M22 0L0 13" stroke="#fff" stroke-width="2.6"/><path d="M0 0L22 13M22 0L0 13" stroke="#c8102e" stroke-width="1"/><path d="M11 0v13M0 6.5h22" stroke="#fff" stroke-width="4"/><path d="M11 0v13M0 6.5h22" stroke="#c8102e" stroke-width="2.2"/></svg>
        English <svg width="9" height="6"><path d="M0 0h9L4.5 6z" fill="#222"/></svg>
      </span>
    </div>
  </nav>
  <h1 class="hero-title">RAVNAAS-LILLEBY</h1>
  <p class="hero-sub">Recruitment and Organizational development</p>
</header>

<section class="feature-band top">
  <div class="feature" style="left:98px">
    <svg width="52" height="50" viewBox="0 0 52 50" fill="#fff"><circle cx="26" cy="12" r="8"/><path d="M12 42c0-10 6-16 14-16s14 6 14 16z"/><circle cx="9" cy="17" r="6"/><path d="M0 40c0-8 4-12 10-12l2 12z"/><circle cx="43" cy="17" r="6"/><path d="M52 40c0-8-4-12-10-12l-2 12z"/></svg>
    <h3>Recruitment</h3><p>We are nationwide including through cooperation agreements.</p>
  </div>
  <span class="divider" style="left:419px"></span>
  <div class="feature" style="left:451px">
    <svg width="54" height="52" viewBox="0 0 54 52"><circle cx="20" cy="30" r="13" fill="none" stroke="#fff" stroke-width="8" stroke-dasharray="5 3"/><circle cx="40" cy="13" r="8" fill="none" stroke="#fff" stroke-width="5" stroke-dasharray="4 2"/></svg>
    <h3>Organizational development</h3><p>We are nationwide including through cooperation agreements.</p>
  </div>
  <span class="divider" style="left:784px"></span>
  <div class="feature" style="left:818px">
    <svg width="40" height="50" viewBox="0 0 40 50" fill="#fff"><circle cx="20" cy="13" r="11"/><path d="M2 46c0-13 8-19 18-19s18 6 18 19z"/></svg>
    <h3>Personality test</h3><p>We are nationwide including through cooperation agreements.</p>
  </div>
</section>

<main>
  <section class="compass" aria-label="Compass">
    <div class="compass-dial" role="img" aria-label="Illustration of a maritime compass rose with a black star and a blue graduated dial"></div>
    <span class="compass-point" style="left:606px; top:750px">N</span>
    <span class="compass-point" style="left:403px; top:954px">W</span>
    <span class="compass-point" style="left:802px; top:954px">E</span>
    <span class="compass-point" style="left:606px; top:1158px">S</span>
  </section>

  <div class="gauge-label" style="left:308px">ENERGY</div>
  <svg class="gauge" style="left:335px" width="190" height="52" viewBox="0 0 190 52" aria-label="Energy level">
    <rect x="1.5" y="1.5" width="178" height="49" fill="#fff" stroke="#555" stroke-width="2"/>
    <rect x="180" y="18" width="8" height="16" fill="#777"/>
    <g fill="#2f9a3f">
      <rect x="8" y="7" width="4" height="38"/><rect x="15" y="7" width="4" height="38"/><rect x="22" y="7" width="4" height="38"/><rect x="29" y="7" width="4" height="38"/><rect x="36" y="7" width="4" height="38"/><rect x="43" y="7" width="4" height="38"/><rect x="50" y="7" width="4" height="38"/><rect x="57" y="7" width="4" height="38"/><rect x="64" y="7" width="4" height="38"/><rect x="71" y="7" width="4" height="38"/><rect x="78" y="7" width="4" height="38"/><rect x="85" y="7" width="4" height="38"/>
    </g>
    <g fill="#e0313c">
      <rect x="92" y="7" width="4" height="38"/><rect x="99" y="7" width="4" height="38"/><rect x="106" y="7" width="4" height="38"/><rect x="113" y="7" width="4" height="38"/><rect x="120" y="7" width="4" height="38"/>
    </g>
  </svg>

  <div class="gauge-label" style="left:650px">PROBLEM SOLVE</div>
  <svg class="gauge" style="left:678px" width="190" height="52" viewBox="0 0 190 52" aria-label="Problem solving level">
    <rect x="1.5" y="1.5" width="178" height="49" fill="#fff" stroke="#555" stroke-width="2"/>
    <rect x="180" y="18" width="8" height="16" fill="#777"/>
    <g fill="#2f9a3f">
      <rect x="8" y="7" width="4" height="38"/><rect x="15" y="7" width="4" height="38"/><rect x="22" y="7" width="4" height="38"/><rect x="29" y="7" width="4" height="38"/><rect x="36" y="7" width="4" height="38"/><rect x="43" y="7" width="4" height="38"/><rect x="50" y="7" width="4" height="38"/><rect x="57" y="7" width="4" height="38"/><rect x="64" y="7" width="4" height="38"/><rect x="71" y="7" width="4" height="38"/><rect x="78" y="7" width="4" height="38"/>
    </g>
    <g fill="#e0313c">
      <rect x="85" y="7" width="4" height="38"/><rect x="92" y="7" width="4" height="38"/><rect x="99" y="7" width="4" height="38"/><rect x="106" y="7" width="4" height="38"/><rect x="113" y="7" width="4" height="38"/><rect x="120" y="7" width="4" height="38"/>
    </g>
  </svg>

  <div class="results-head" style="left:266px">
    <svg width="54" height="54" viewBox="0 0 54 54"><circle cx="27" cy="27" r="24" fill="none" stroke="#23398a" stroke-width="4"/><circle cx="27" cy="27" r="15" fill="none" stroke="#23398a" stroke-width="3"/><line x1="27" y1="5" x2="27" y2="49" stroke="#23398a" stroke-width="3"/><line x1="5" y1="27" x2="49" y2="27" stroke="#23398a" stroke-width="3"/></svg>
    LISTENING
  </div>
  <div class="results-head" style="left:693px">
    <svg width="48" height="40" viewBox="0 0 48 40" fill="#23398a"><path d="M2 14h10l22-12v34L12 24H2z"/><rect x="8" y="24" width="7" height="14"/><rect x="38" y="15" width="8" height="5"/></svg>
    SENDING
  </div>

  <table class="result-table" style="left:270px" aria-label="Listening results">
    <tr><td class="no">NO</td><td class="no">NO</td></tr>
    <tr><td class="yes">YES</td><td class="no">NO</td></tr>
    <tr><td class="yes">YES</td><td class="no">NO</td></tr>
    <tr><td class="yes">YES</td><td class="no">NO</td></tr>
    <tr><td class="yes">YES</td><td class="yes">YES</td></tr>
    <tr><td class="yes">YES</td><td class="yes">YES</td></tr>
  </table>
  <ul class="scores">
    <li>------ 1 ------</li><li>------ 2 ------</li><li>------ 2 ------</li><li>------ 1 ------</li><li>------ 4 ------</li><li>------ 5 ------</li>
  </ul>
  <table class="result-table" style="left:693px" aria-label="Sending results">
    <tr><td class="no">NO</td><td class="no">NO</td></tr>
    <tr><td class="no">NO</td><td class="no">NO</td></tr>
    <tr><td class="no">NO</td><td class="no">NO</td></tr>
    <tr><td class="yes">YES</td><td class="no">NO</td></tr>
    <tr><td class="yes">YES</td><td class="no">NO</td></tr>
    <tr><td class="yes">YES</td><td class="yes">YES</td></tr>
  </table>

  <dl class="profile">
    <dt>Name :</dt><dd>Ola Eksempel</dd>
    <dt>Company :</dt><dd>Finibus Bonorum et Malo</dd>
    <dt>Profile :</dt><dd>At vero eos et accusamus et iusto odio dignissimos ducimus qui blanditiis praesentium voluptatum deleniti atque corrupti quos dolores</dd>
  </dl>
</main>

<section class="feature-band bottom">
  <div class="feature" style="left:98px">
    <svg width="48" height="44" viewBox="0 0 48 40" fill="#fff"><path d="M2 14h10l22-12v34L12 24H2z"/><rect x="8" y="24" width="7" height="14"/><rect x="38" y="15" width="8" height="5"/></svg>
    <h3>Send</h3><p>We are nationwide including through cooperation agreements.</p>
  </div>
  <span class="divider" style="left:419px"></span>
  <div class="feature" style="left:448px">
    <svg width="54" height="54" viewBox="0 0 54 54"><circle cx="27" cy="27" r="24" fill="none" stroke="#fff" stroke-width="4"/><circle cx="27" cy="27" r="15" fill="none" stroke="#fff" stroke-width="3"/><line x1="27" y1="5" x2="27" y2="49" stroke="#fff" stroke-width="3"/><line x1="5" y1="27" x2="49" y2="27" stroke="#fff" stroke-width="3"/></svg>
    <h3>Receive</h3><p>We are nationwide including through cooperation agreements.</p>
  </div>
  <span class="divider" style="left:784px"></span>
  <div class="feature" style="left:812px">
    <svg width="56" height="50" viewBox="0 0 56 50" fill="#fff"><rect x="22" y="2" width="10" height="10"/><rect x="14" y="12" width="26" height="12"/><path d="M4 26h48l-8 14H12z"/><path d="M2 44q7-5 13 0t13 0 13 0 13 0v3q-7 4-13 0t-13 0-13 0-13 0z"/></svg>
    <h3>Clients business</h3><p>We are nationwide including through cooperation agreements.</p>
  </div>
</section>

<footer class="site-footer">
  <h4 class="footer-title" style="left:99px">RAVNAAS-LILLEBY GROUP AS</h4>
  <p class="about">Ravnaas-Lilleby Group AS (RLG) is an active counselor nationally and internationally in the field of recruitment and organizational development / change.</p>
  <div class="socials"><span aria-label="Social link"></span><span aria-label="Social link"></span><span aria-label="Social link"></span></div>

  <h4 class="footer-title" style="left:575px">QUICK LINKS</h4>
  <ul class="quick-links">
    <li>Help</li><li>FAQ</li><li>Support</li><li>Sitemap</li><li>Terms Of Use</li><li>Privacy Statement</li>
  </ul>

  <h4 class="footer-title" style="left:797px">CONTACT US</h4>
  <ul class="contact-list">
    <li><svg width="10" height="14" viewBox="0 0 10 14"><path d="M5 0a5 5 0 0 1 5 5c0 4-5 9-5 9S0 9 0 5a5 5 0 0 1 5-5z" fill="#fff"/><circle cx="5" cy="5" r="2" fill="#1b1b1d"/></svg>Havnegata 42, 2nd floor,<br>0250 Oslo</li>
    <li><svg width="13" height="13" viewBox="0 0 13 13"><path d="M2 0l3 3-1.5 2a8 8 0 0 0 4.5 4.5L10 8l3 3-2 2C5 13 0 8 0 2z" fill="#fff"/></svg>21 00 48 73</li>
    <li><svg width="14" height="10" viewBox="0 0 14 10"><rect width="14" height="10" fill="#fff"/><path d="M0 0l7 6 7-6" fill="none" stroke="#1b1b1d" stroke-width="1.4"/></svg>post@ravnaas-lilleby.example</li>
  </ul>

  <div class="footer-rule"></div>
  <p class="copyright">Copyrights © 2017, Ravnaas-Lilleby Group . All rights reserved.</p>
</footer>

</body>
</html>
```